Commercial Rooftop Solar business needs a website

We need a website with fantastic appeal for a new company based in Melbourne called Tallow Ridge Energy. We design and install solar energy systems for commercial applications across Australia. Our market is to focus on small to medium businesses looking for solar solutions, but we will also provide our service for residential customers. We would like a beautiful 'front page' feel to our home page, using photographs of solar PV systems and/or natural imagery. Our logo uses the colours orange and black, which could easily be echoed in photographic imagery of sunset and sunrise, for example. The design should communicate quiet confidence and professionalism to a corporate marketplace.

NEW POINTS FOR BRIEF: This design also needs to be flexible to allow for additional future content, including a Support page with sub pages, FAQ's, and a Blog.

As part of this design project, we will require the coding for the website to be completed by the designer.

We have seen some websites, which we like the look and feel of: these are listed below.

brightvanepower.com.au:

• Beautiful images underlaying brief text selling points.
• Simple ‘front cover’ style home page with elegant drop-down menu, stylish simple font style.
• Home page invites exploration through the menu links, rather than trying to provide all the information up front.
• Company logo and name in the top left hand corner, contact details accessible at top right hand, seems consistent in most sites.

kelpworks.com.au

rumbofield.com:
• Same element as the others is the front-page style home page with beautiful images underlying text.

We have a webpage that we started uploading content to. You can use some of the content there in your designs: www.tallowridgeenergy.com.au

Technical Specifications:
PAGES:

Home

About Us

Solutions - Commercial
- Residential

Products - Solar Panels - Vorla Heron, Vorla TELD, Vorla QB
- Solar Inverters - Kestamo, BrilQuill
- Monitoring systems - Dunmere Metrics
- Batteries - RW

- Datasheets have been provided for reference but if it's too much work, you can use generic text and we will provide content later.

Contact Us

FUTURE PAGES (Please consider in structure, where links could be placed):

Support

FAQ's

Blog.

We could provide some content for the Support page soon, but the Blog and FAQ's are future pages which we don't want highlighted in the design as we don't yet have content.

Phone: 1800 7 BIRCH
Email: sales@tallowridgeenergy.com.au

Currently, I do not have images and text available. Please
use placeholders in the meantime. The final text and images will be uploaded for the winner once a winning design has been selected.

Target Market(s)

Primary focus is on small to medium sized business owners. Those owners will have a house which may be suitable for solar so we want to cater to residential deeper in the website.

Industry/Entity Type

Solar Energy

Coding

Coded - Design and coding required

Number of Pages Required

5+ page

Colors
f78f20
0255a3

Requirements
Must have
• Logo as per attachments.
Nice to have
• Logo can have alternate colours Eg. White on Orange or Black etc. provided colour correct logo is shown somewhere eg. footer or contact page.
• In the active site, I'd like to have:
• Very slowly zooming images - barely perceptible.
• Title text that rolls into place
• Subtle movements
• See https://plumtally.com.au/ for example

```html
<!DOCTYPE html>
<html lang="en">
<head>
<meta charset="utf-8">
<title>Tallow Ridge Energy</title>
<link rel="stylesheet" href="https://fonts.googleapis.com/css2?family=Open+Sans:wght@400;600;700&family=Raleway:wght@500;600;700;800&display=swap">
<style>
  :root {
    --orange: #f0581f;
    --orange-soft: #f78f20;
    --ink: #2a2a2a;
    --text: #7a7a7a;
    --line: #dcdcdc;
    --grey-band: #f5f5f5;
    --white: #ffffff;
    --footer: #1b1b1b;
    --footer-text: #d8d8d8;
  }
  * { box-sizing: border-box; margin: 0; padding: 0; }
  html, body { width: 1200px; height: 2667px; overflow: hidden; }
  body { font-family: "Open Sans", Arial, sans-serif; color: var(--ink); background: var(--white); position: relative; }
  ul { list-style: none; }

  /* Hero */
  .hero { position: relative; height: 571px; overflow: hidden; }
  .hero-photo {
    position: absolute; inset: 0;
    background:
      radial-gradient(ellipse 380px 260px at 640px 360px, rgba(255,170,60,0.95), rgba(230,110,30,0.55) 45%, rgba(0,0,0,0) 75%),
      linear-gradient(180deg, #4a4f5a 0%, #5b5550 30%, #7a5a3a 55%, #8a5326 68%, #3d2a1e 82%, #2a241f 100%);
  }
  .hero-shade { position: absolute; inset: 0; background: rgba(20,20,25,0.18); }
  .site-header { position: absolute; top: 0; left: 0; right: 0; height: 118px; display: flex; align-items: center; padding: 0 75px; }
  .brand { display: flex; align-items: center; gap: 12px; color: var(--white); font-family: "Raleway", sans-serif; font-weight: 700; font-size: 22px; letter-spacing: 0.5px; }
  .brand-dot { width: 40px; height: 40px; border-radius: 50%; background: var(--white); }
  .main-nav { position: absolute; left: 445px; top: 48px; display: flex; align-items: center; gap: 30px; font-family: "Raleway", sans-serif; font-weight: 700; font-size: 15px; color: var(--white); }
  .main-nav .active { color: var(--orange-soft); }
  .caret { display: inline-block; margin-left: 6px; border: 5px solid transparent; border-top-color: var(--white); transform: translateY(3px); }
  .search-icon { margin-left: 6px; }
  .header-phone { position: absolute; left: 950px; top: 44px; display: flex; align-items: center; gap: 12px; color: var(--white); font-size: 16px; font-weight: 600; }
  .phone-badge { width: 28px; height: 28px; border-radius: 50%; background: var(--orange); display: flex; align-items: center; justify-content: center; }

  .hero-copy { position: absolute; top: 168px; left: 0; right: 0; text-align: center; color: var(--white); }
  .hero-title { font-family: "Open Sans", sans-serif; font-weight: 700; font-size: 58px; letter-spacing: 0.5px; text-shadow: 0 2px 6px rgba(0,0,0,0.35); }
  .hero-lead { margin: 18px auto 0; width: 720px; font-size: 24px; line-height: 1.6; font-weight: 600; text-shadow: 0 1px 4px rgba(0,0,0,0.4); }
  .hero-button { display: inline-block; margin-top: 26px; width: 192px; height: 46px; line-height: 44px; border: 2px solid var(--white); border-radius: 4px; font-size: 15px; font-weight: 700; color: var(--white); }
  .scroll-cue { position: absolute; left: 586px; top: 484px; width: 30px; height: 50px; border: 2px solid var(--white); border-radius: 15px; display: flex; align-items: center; justify-content: center; }
  .slide-arrow { position: absolute; top: 262px; width: 38px; height: 50px; background: rgba(255,255,255,0.22); display: flex; align-items: center; justify-content: center; }
  .slide-arrow.prev { left: 0; }
  .slide-arrow.next { right: 0; }

  /* Shared section heads */
  .section-title { text-align: center; font-family: "Raleway", sans-serif; font-weight: 800; font-size: 34px; color: var(--ink); letter-spacing: 0.5px; }
  .section-title::after { content: ""; display: block; width: 80px; height: 3px; background: var(--orange); margin: 24px auto 0; }

  /* Welcome */
  .welcome { height: 589px; padding-top: 82px; }
  .welcome-intro { width: 740px; margin: 36px auto 0; text-align: center; font-size: 13px; line-height: 1.9; color: var(--text); }
  .services { display: grid; grid-template-columns: repeat(3, 357px); row-gap: 58px; margin: 60px 0 0 98px; }
  .service { display: flex; gap: 20px; }
  .service-icon { width: 80px; height: 80px; flex: none; border: 1px solid var(--line); border-radius: 50%; display: flex; align-items: center; justify-content: center; }
  .service h3 { font-family: "Raleway", sans-serif; font-weight: 600; font-size: 19px; margin-top: 8px; }
  .service p { margin-top: 12px; font-size: 12.5px; line-height: 1.9; color: var(--text); width: 200px; }

  /* Solutions */
  .solutions { height: 783px; background: var(--grey-band); padding-top: 62px; }
  .solution-grid { display: flex; gap: 56px; margin: 60px 0 0 98px; }
  .solution { width: 474px; }
  .solution-photo { height: 262px; border: 6px solid var(--white); box-shadow: 0 0 0 1px #e4e4e4; }
  .photo-field { background: linear-gradient(180deg, #f2b441 0%, #f08a2c 30%, #d9642a 48%, #b34a3c 62%, #8c3b40 100%); }
  .photo-roof { background: linear-gradient(180deg, #9d9a6a 0%, #c8c3a8 28%, #8a9db3 45%, #6f86a3 62%, #5e5a58 78%, #3b3938 100%); }
  .solution h3 { margin-top: 34px; font-family: "Raleway", sans-serif; font-weight: 600; font-size: 27px; letter-spacing: 0.5px; }
  .solution h3::after { content: ""; display: block; width: 80px; height: 3px; background: var(--orange); margin-top: 10px; }
  .solution p { margin-top: 26px; font-size: 13px; line-height: 1.85; color: var(--text); }
  .read-more { display: inline-block; margin-top: 24px; width: 122px; height: 40px; line-height: 38px; text-align: center; border: 1px solid #c9c9c9; border-radius: 4px; font-size: 12px; font-weight: 700; color: var(--orange); }

  /* Products */
  .products { height: 347px; padding-top: 62px; }
  .brand-row { display: flex; gap: 29px; margin: 58px 0 0 98px; }
  .brand-tile { width: 178px; height: 88px; border: 3px solid #e6e6e6; display: flex; align-items: center; justify-content: center; font-family: "Open Sans", sans-serif; font-weight: 600; font-size: 24px; color: #8a8a8a; }

  /* Footer */
  .site-footer { position: absolute; top: 2290px; left: 0; width: 1200px; height: 377px; background: var(--footer); border-top: 4px solid var(--orange); color: var(--footer-text); }
  .footer-brand { position: absolute; left: 98px; top: 80px; display: flex; flex-direction: column; align-items: center; gap: 10px; color: var(--white); font-family: "Raleway", sans-serif; font-weight: 700; font-size: 18px; width: 150px; text-align: center; line-height: 1.3; }
  .footer-brand .brand-dot { width: 42px; height: 42px; }
  .footer-col { position: absolute; top: 54px; }
  .footer-col h4 { font-family: "Raleway", sans-serif; font-weight: 700; font-size: 16px; color: var(--white); margin-bottom: 24px; }
  .col-contact { left: 310px; }
  .contact-line { display: flex; gap: 16px; font-size: 12px; line-height: 1.8; margin-bottom: 12px; }
  .contact-line svg { flex: none; margin-top: 3px; }
  .col-signup { left: 622px; width: 285px; }
  .col-signup p { font-size: 11.5px; line-height: 1.8; }
  .email-field { margin-top: 16px; height: 42px; background: var(--white); color: #555; font-size: 11px; padding: 13px 12px; }
  .subscribe { margin-top: 12px; width: 113px; height: 40px; background: var(--orange); color: var(--white); font-weight: 700; font-size: 13px; display: flex; align-items: center; justify-content: center; }
  .col-links { left: 985px; }
  .col-links li { font-size: 12px; line-height: 2.05; }
  .copyright { position: absolute; left: 0; right: 0; top: 327px; text-align: center; font-size: 11.5px; color: var(--white); }
</style>
</head>
<body>

<header class="hero">
  <div class="hero-photo" role="img" aria-label="City skyline at sunset with the sun glowing between towers over the water"></div>
  <div class="hero-shade"></div>

  <div class="site-header">
    <div class="brand"><span class="brand-dot"></span>Tallow Ridge Energy</div>
    <nav class="main-nav">
      <span class="active">HOME</span>
      <span>ABOUT US</span>
      <span>SOLUTIONS<i class="caret"></i></span>
      <span>CONTACT US</span>
      <svg class="search-icon" width="15" height="15" viewBox="0 0 16 16"><circle cx="6.5" cy="6.5" r="5" fill="none" stroke="#fff" stroke-width="2"/><line x1="10.5" y1="10.5" x2="15" y2="15" stroke="#fff" stroke-width="2.4" stroke-linecap="round"/></svg>
    </nav>
    <div class="header-phone">
      <span class="phone-badge"><svg width="14" height="14" viewBox="0 0 24 24"><path fill="#fff" d="M6.6 10.8a15.5 15.5 0 0 0 6.6 6.6l2.2-2.2c.3-.3.7-.4 1-.2 1.1.4 2.3.6 3.6.6.6 0 1 .4 1 1V20c0 .6-.4 1-1 1A17 17 0 0 1 3 4c0-.6.4-1 1-1h3.5c.6 0 1 .4 1 1 0 1.3.2 2.5.6 3.6.1.3 0 .7-.2 1z"/></svg></span>
      1 800 555 0142
    </div>
  </div>

  <div class="slide-arrow prev"><svg width="12" height="20" viewBox="0 0 12 20"><path d="M10 2 2 10l8 8" fill="none" stroke="#fff" stroke-width="2"/></svg></div>
  <div class="slide-arrow next"><svg width="12" height="20" viewBox="0 0 12 20"><path d="M2 2l8 8-8 8" fill="none" stroke="#fff" stroke-width="2"/></svg></div>

  <div class="hero-copy">
    <h1 class="hero-title">TALLOW RIDGE ENERGY</h1>
    <p class="hero-lead">We design and install solar energy systems for commercial applications across Australia</p>
    <span class="hero-button">GET MORE INFO</span>
  </div>
  <div class="scroll-cue"><svg width="14" height="22" viewBox="0 0 14 22"><path d="M2 4l5 5 5-5M2 12l5 5 5-5" fill="none" stroke="#fff" stroke-width="2"/></svg></div>
</header>

<section class="welcome">
  <h2 class="section-title">WELCOME TO TALLOW RIDGE ENERGY</h2>
  <p class="welcome-intro">We plan, build and care for solar systems that help Australian businesses cut power costs, stay in control of energy use and run cleaner every single day.</p>
  <div class="services">
    <div class="service">
      <div class="service-icon"><svg width="36" height="36" viewBox="0 0 32 32"><rect x="4" y="7" width="20" height="20" rx="3" fill="none" stroke="#f0581f" stroke-width="2.5"/><path d="M13 19l2-6 12-12 4 4-12 12z" fill="#f0581f"/></svg></div>
      <div><h3>System Design</h3><p>Layouts shaped to your roof, load and budget.</p></div>
    </div>
    <div class="service">
      <div class="service-icon"><svg width="38" height="38" viewBox="0 0 32 32"><circle cx="12" cy="18" r="7" fill="none" stroke="#f0581f" stroke-width="4" stroke-dasharray="3 2.5"/><circle cx="12" cy="18" r="2.5" fill="#f0581f"/><circle cx="24" cy="9" r="5" fill="none" stroke="#f0581f" stroke-width="3" stroke-dasharray="2.5 2"/></svg></div>
      <div><h3>Operational Management</h3><p>Ongoing checks that keep every array running well.</p></div>
    </div>
    <div class="service">
      <div class="service-icon"><svg width="34" height="34" viewBox="0 0 32 32"><path d="M27 5a7 7 0 0 0-9 9L5 27l3 3 13-13a7 7 0 0 0 9-9l-4 4-4-1-1-4z" fill="#f0581f"/></svg></div>
      <div><h3>Installation</h3><p>Accredited crews fitting panels safely and on time.</p></div>
    </div>
    <div class="service">
      <div class="service-icon"><svg width="38" height="38" viewBox="0 0 32 32"><circle cx="16" cy="16" r="8" fill="#f0581f"/><g stroke="#f0581f" stroke-width="2.5" stroke-linecap="round"><line x1="16" y1="2" x2="16" y2="5"/><line x1="16" y1="27" x2="16" y2="30"/><line x1="2" y1="16" x2="5" y2="16"/><line x1="27" y1="16" x2="30" y2="16"/><line x1="6" y1="6" x2="8" y2="8"/><line x1="24" y1="24" x2="26" y2="26"/><line x1="6" y1="26" x2="8" y2="24"/><line x1="24" y1="8" x2="26" y2="6"/></g><path d="M17 10l-4 7h3l-1 5 4-7h-3z" fill="#fff"/></svg></div>
      <div><h3>Solar Irrigation</h3><p>Solar pumping for farms, gardens and open land.</p></div>
    </div>
    <div class="service">
      <div class="service-icon"><svg width="40" height="26" viewBox="0 0 40 26"><rect x="2" y="3" width="32" height="20" rx="3" fill="none" stroke="#f0581f" stroke-width="3"/><rect x="6" y="7" width="24" height="12" fill="#f0581f"/><rect x="35" y="9" width="3" height="8" fill="#f0581f"/></svg></div>
      <div><h3>Energy Storage</h3><p>Battery storage to hold daytime power for later.</p></div>
    </div>
    <div class="service">
      <div class="service-icon"><svg width="30" height="38" viewBox="0 0 24 32"><path d="M12 2a9 9 0 0 0-5 16.5V22h10v-3.5A9 9 0 0 0 12 2z" fill="none" stroke="#f0581f" stroke-width="2.5"/><rect x="8" y="24" width="8" height="2.5" fill="#f0581f"/><rect x="9" y="28" width="6" height="2.5" fill="#f0581f"/></svg></div>
      <div><h3>Feasibility Study</h3><p>Clear reports on cost, yield and payback time.</p></div>
    </div>
  </div>
</section>

<section class="solutions">
  <h2 class="section-title">OUR SOLUTIONS</h2>
  <div class="solution-grid">
    <article class="solution">
      <div class="solution-photo photo-field" role="img" aria-label="Large field of solar panels under an orange sunset sky"></div>
      <h3>COMMERCIAL</h3>
      <p>Solar for offices, warehouses and shops that want lower running costs. We size each system to the way your site uses power, manage approvals and grid connection, and hand over a plant built to perform for decades with full monitoring.</p>
      <span class="read-more">READ MORE &gt;&gt;</span>
    </article>
    <article class="solution">
      <div class="solution-photo photo-roof" role="img" aria-label="Solar panels mounted on a house roof with autumn trees behind"></div>
      <h3>RESIDENTIAL</h3>
      <p>Clean power for the family home, designed around your roof and daily routine. We take care of panels, inverters and batteries from first quote to switch on, so you can start saving on bills from the very first sunny day.</p>
      <span class="read-more">READ MORE &gt;&gt;</span>
    </article>
  </div>
</section>

<section class="products">
  <h2 class="section-title">OUR PRODUCTS</h2>
  <div class="brand-row">
    <div class="brand-tile">Halvex</div>
    <div class="brand-tile">Corvane</div>
    <div class="brand-tile">Lumetra</div>
    <div class="brand-tile">Pinewick</div>
    <div class="brand-tile">Oddmere</div>
  </div>
</section>

<footer class="site-footer">
  <div class="footer-brand"><span class="brand-dot"></span>Tallow Ridge Energy</div>

  <div class="footer-col col-contact">
    <h4>CONTACT US</h4>
    <div class="contact-line">
      <svg width="14" height="18" viewBox="0 0 14 18"><path d="M7 1a6 6 0 0 0-6 6c0 4.5 6 10 6 10s6-5.5 6-10a6 6 0 0 0-6-6z" fill="none" stroke="#ddd" stroke-width="1.5"/><circle cx="7" cy="7" r="2" fill="#ddd"/></svg>
      <span>Tallow Ridge Energy<br>Harrow Lane, Fenmoor, Vic.</span>
    </div>
    <div class="contact-line">
      <svg width="16" height="16" viewBox="0 0 24 24"><path fill="none" stroke="#ddd" stroke-width="1.8" d="M6.6 10.8a15.5 15.5 0 0 0 6.6 6.6l2.2-2.2c.3-.3.7-.4 1-.2 1.1.4 2.3.6 3.6.6.6 0 1 .4 1 1V20c0 .6-.4 1-1 1A17 17 0 0 1 3 4c0-.6.4-1 1-1h3.5c.6 0 1 .4 1 1 0 1.3.2 2.5.6 3.6.1.3 0 .7-.2 1z"/></svg>
      <span>Phone : +61 3 5550 1876</span>
    </div>
    <div class="contact-line">
      <svg width="18" height="14" viewBox="0 0 18 14"><rect x="1" y="1" width="16" height="12" fill="none" stroke="#ddd" stroke-width="1.5"/><path d="M1 1l8 7 8-7" fill="none" stroke="#ddd" stroke-width="1.5"/></svg>
      <span>admin@tallowridgeenergy.com.au</span>
    </div>
  </div>

  <div class="footer-col col-signup">
    <h4>SIGN UP TO RECEIVE EMAIL</h4>
    <p>Get project news, rebate updates and simple tips for getting more from solar.</p>
    <div class="email-field">Enter Email</div>
    <div class="subscribe">SUBSCRIBE</div>
  </div>

  <div class="footer-col col-links">
    <h4>QUICK LINKS</h4>
    <ul>
      <li>Home</li>
      <li>About Us</li>
      <li>Solutions</li>
      <li>Projects</li>
      <li>Blog</li>
      <li>Contact Us</li>
    </ul>
  </div>

  <p class="copyright">Copyright © Tallow Ridge Energy 2017. All rights reserved.</p>
</footer>

</body>
</html>
```